I need a business card designed using the logo provided either vertical or horizontal......Harbourline Property Group is an Australian based real estate company that caters for the upper end of the market so the design of the business card "must reflect" the companies image!!
Colour combinations are optional but "must be realistic" and must be able to be accurately useable CMYK colours.
Please consider that any colours used "must be able to be used" and be suitable in following designs for "pull out banner signs" and "real estate signs".
The colours and the font in the attached designs are for example and other combinations are encouraged.
Target Market(s)
The High End of the Australian real estate market
Industry/Entity Type
Business
Contact Information for Business Card
Logo - Business Name - Director + Licensed Real Estate Agent - Mobile Number (Cell Phone) - Business Number - Fax - Email Address - Web address
Requirements
Must have
- Designs and colours (CMYK) that can easily be interpreted by an Australian printer.
Nice to have
- Some alternative ideas on colour and font..........the ones provided are ok and have been provided as an example but I am looking for alternative ideas
Should not have
- Loud, overly bright colours. Designs that do not reflect the professional standards of the business.
- Designs that look good on a computer monitor but can not be re-created on a printing press.............this is most important when it comes to shading etc.

```html
<!DOCTYPE html>
<html lang="en">
<head>
<meta charset="utf-8">
<title>Harbourline Property Group – Business Card</title>
<link href="https://fonts.googleapis.com/css2?family=PT+Sans:wght@400;700&display=swap" rel="stylesheet">
<style>
  :root {
    --backdrop: #2b2522;
    --gold: #b3802a;
    --cream: #eedfb0;
    --ink: #0e0e0e;
    --ink-soft: #262626;
    --type-light: #f1ead8;
    --type-gold: #c8902e;
  }
  * { margin: 0; padding: 0; box-sizing: border-box; }
  html, body {
    width: 1200px; height: 844px; overflow: hidden;
    background: var(--backdrop);
    font-family: "PT Sans", Arial, sans-serif;
  }
  .stage {
    position: relative; width: 1200px; height: 844px;
    display: flex; align-items: center; justify-content: center; gap: 60px;
  }
  .card {
    position: relative; width: 500px; height: 290px; overflow: hidden;
    box-shadow: 0 14px 30px rgba(0,0,0,.45);
  }

  /* Contact side */
  .card--contact {
    background: linear-gradient(100deg, var(--ink) 0%, var(--ink) 55%, var(--ink-soft) 100%);
  }
  .band { position: absolute; left: 0; width: 100%; }
  .band--gold-top { top: 0; height: 22px; background: var(--gold); }
  .band--cream-top { top: 22px; height: 5px; background: var(--cream); }
  .band--cream-bottom { bottom: 22px; height: 5px; background: var(--cream); }
  .band--gold-bottom { bottom: 0; height: 22px; background: var(--gold); }

  .identity { position: absolute; left: 190px; top: 56px; }
  .identity__name {
    color: var(--type-light); font-size: 19px; font-weight: 400;
    letter-spacing: .5px; padding-bottom: 3px;
    border-bottom: 1px solid var(--type-light);
  }
  .identity__role { color: var(--type-gold); font-size: 15px; margin-top: 2px; }

  .contact-list {
    position: absolute; left: 190px; right: 30px; top: 128px;
    list-style: none; text-align: center;
    color: var(--type-gold); font-size: 14.5px; line-height: 19px;
  }
  .address {
    position: absolute; left: 30px; right: 30px; bottom: 44px;
    color: var(--type-light); font-size: 14px; text-align: center; letter-spacing: .2px;
  }

  /* Brand side */
  .card--brand {
    background: var(--gold);
    display: flex; align-items: center; justify-content: center; gap: 14px;
  }
  .brand-mark { width: 14px; height: 14px; background: var(--cream); flex: none; }
  .brand-name {
    color: var(--cream); font-size: 26px; font-weight: 700;
    letter-spacing: 1.5px; text-transform: uppercase; line-height: 1.15;
  }
</style>
</head>
<body>
<main class="stage">
  <section class="card card--contact" aria-label="Business card, contact side">
    <div class="band band--gold-top"></div>
    <div class="band band--cream-top"></div>

    <div class="identity">
      <h1 class="identity__name">DANIEL WHITCOMBE</h1>
      <p class="identity__role">Managing Director</p>
    </div>

    <ul class="contact-list">
      <li>044-318-2207</li>
      <li>123-556-0412</li>
      <li>hello@harbourline.com.au</li>
      <li>www.harbourline.com.au</li>
    </ul>

    <p class="address">88 Esplanade Row | Sydney, NSW | 2000</p>

    <div class="band band--cream-bottom"></div>
    <div class="band band--gold-bottom"></div>
  </section>

  <section class="card card--brand" aria-label="Business card, brand side">
    <span class="brand-mark" aria-hidden="true"></span>
    <p class="brand-name">Harbourline<br>Property Group</p>
  </section>
</main>
</body>
</html>
```